Product Description Graphic

We are designing a new product and need a better graphic to describe it.

We are not worried about names of the modules yet but want to be descriptive of capabilities. Right now "Present & CMA" should really be "Presentations & CMA".

I overall like the shape of the triangle and the arrow for Contacts but this is a very unsophisticated graphic done by a non-designer. Also need to better show that each block of capabilites will also have paywall capabilities.

Target Market(s)

Real Estate Brokerage Firms and Real Estate Agents

Industry/Entity Type

Real Estate

Colors

Designer to choose colors to be used in the design.

Requirements
Must have
• Sophisticated design. Paywall description embedded.

```html
<!DOCTYPE html>
<html lang="en">
<head>
<meta charset="utf-8">
<title>Product Capabilities Pyramid</title>
<link rel="stylesheet" href="https://fonts.googleapis.com/css2?family=Nunito+Sans:wght@700;800&display=swap">
<style>
  :root {
    --bg: #ffffff;
    --ink: #111111;
    --hatch: rgba(40, 60, 120, 0.55);
    --top-block: #3f9dd6;
    --email-band: #65b6e8;
    --websites-chip: #8fcbf0;
    --present-dark: #1290dd;
    --present-bright: #1aa3ee;
    --contacts: #5fa8e8;
    --arrow-stem: #4394d9;
    --base-left: #5ba7dd;
    --base-right: #2fa1e5;
    --mobile-chip: #46b6f3;
    --label: #ffffff;
  }
  html, body {
    margin: 0;
    padding: 0;
    width: 1200px;
    height: 1200px;
    overflow: hidden;
    background: var(--bg);
  }
  .canvas {
    display: block;
    width: 1200px;
    height: 1200px;
    font-family: "Nunito Sans", "Avenir Next", sans-serif;
  }
  .top-block { fill: var(--top-block); }
  .email-band { fill: var(--email-band); opacity: 0.92; }
  .websites-chip { fill: var(--websites-chip); }
  .present-dark { fill: var(--present-dark); }
  .present-bright { fill: var(--present-bright); }
  .contacts-head { fill: var(--contacts); }
  .arrow-stem { fill: var(--arrow-stem); }
  .base-left { fill: var(--base-left); }
  .base-right { fill: var(--base-right); }
  .mobile-chip { fill: var(--mobile-chip); }
  .paywall-hatch { fill: url(#hatch); }
  .hatch-line { stroke: var(--hatch); stroke-width: 1.2; }
  .legend-line { stroke: #555; stroke-width: 1.2; }
  .label { fill: var(--label); font-weight: 800; font-size: 17px; }
  .label-contacts { fill: var(--label); font-weight: 800; font-size: 24px; letter-spacing: 0.5px; }
  .legend-text { fill: var(--ink); font-weight: 800; font-size: 17px; }
</style>
</head>
<body>
<svg class="canvas" viewBox="0 0 1200 1200" xmlns="http://www.w3.org/2000/svg">
  <defs>
    <pattern id="hatch" width="20" height="20" patternUnits="userSpaceOnUse" patternTransform="rotate(-45)">
      <line class="hatch-line" x1="0" y1="0" x2="0" y2="20"/>
    </pattern>
  </defs>

  <!-- Top capability block -->
  <g class="block block-top">
    <path class="top-block" d="M590 334 Q596 325 602 334 L668 448 L476 750 L330 750 Q318 750 325 739 Z"/>
    <path class="paywall-hatch" d="M590 334 Q596 325 602 334 L668 448 L476 750 L330 750 Q318 750 325 739 Z"/>
    <path class="email-band" d="M585 447 Q596 434 608 447 L642 506 L588 592 L490 750 L388 750 L364 790 Q363 808 380 808 L400 808 L410 790 Z"/>
  </g>

  <!-- Right capability block -->
  <g class="block block-right">
    <path class="present-dark" d="M670 470 Q676 460 683 470 L860 740 Q865 750 853 750 L690 750 L598 592 Q594 585 600 578 Z"/>
    <path class="paywall-hatch" d="M670 470 Q676 460 683 470 L860 740 Q865 750 853 750 L690 750 L598 592 Q594 585 600 578 Z"/>
    <path class="present-bright" d="M646 508 L796 750 L690 750 L598 592 Q594 585 600 578 Z"/>
  </g>

  <!-- Base blocks -->
  <g class="block block-base">
    <path class="base-left" d="M312 762 L555 762 L555 852 Q555 858 549 858 L264 858 Q255 858 260 850 Z"/>
    <path class="paywall-hatch" d="M312 762 L555 762 L555 852 Q555 858 549 858 L264 858 Q255 858 260 850 Z"/>
    <rect class="websites-chip" x="363" y="762" width="192" height="46" rx="12" opacity="0.9"/>

    <path class="base-right" d="M612 762 L872 762 L924 850 Q928 858 919 858 L618 858 Q612 858 612 852 Z"/>
    <path class="paywall-hatch" d="M612 762 L872 762 L924 850 Q928 858 919 858 L618 858 Q612 858 612 852 Z"/>
    <rect class="mobile-chip" x="612" y="762" width="208" height="46" rx="12"/>
  </g>

  <!-- Contacts arrow -->
  <g class="contacts-arrow">
    <path class="contacts-head" d="M580 606 Q586 598 592 606 L678 742 Q682 750 673 750 L499 750 Q490 750 494 742 Z"/>
    <rect class="arrow-stem" x="565" y="750" width="37" height="108" rx="3"/>
    <text class="label-contacts" x="586" y="737" text-anchor="middle">CONTACTS</text>
  </g>

  <!-- Labels -->
  <text class="label" transform="translate(525 610) rotate(-57)" text-anchor="middle">
    <tspan x="0" y="0">Email Nateure Print</tspan>
    <tspan x="0" y="21">&amp; Social</tspan>
  </text>
  <text class="label" transform="translate(668 650) rotate(57)" text-anchor="middle">
    <tspan x="0" y="0">Presentations</tspan>
    <tspan x="0" y="21">&amp; CMA</tspan>
  </text>
  <text class="label" x="390" y="792">Websites &amp; Leads</text>
  <text class="label" x="630" y="792">Mobile</text>

  <!-- Legend -->
  <g class="legend">
    <line class="legend-line" x1="862" y1="380" x2="890" y2="404"/>
    <line class="legend-line" x1="888" y1="380" x2="910" y2="402"/>
    <line class="legend-line" x1="852" y1="402" x2="886" y2="436"/>
    <line class="legend-line" x1="878" y1="404" x2="910" y2="432"/>
    <line class="legend-line" x1="852" y1="430" x2="860" y2="436"/>
    <text class="legend-text" x="943" y="403">Paywall</text>
    <text class="legend-text" x="943" y="434">Feature</text>
  </g>
</svg>
</body>
</html>
```